Calloway needs a modernized design

We would like a modern update (that can be responsive) to our existing website. Attached are the two existing pages we would like new concepts of - our home page and a page about one of our locations.

Calloway is provides executive offices and virtual office services. Startups, law firms, and financial services are our primary clients. We would like a professional, clean design, leaning towards minimalist. We intend to greatly reduce/eliminate the long paragraphs of text.

Requirements
Must have
• A design that can be responsive
Nice to have
• Large image(s) on home page that rotate.

```html
<!DOCTYPE html>
<html lang="en">
<head>
<meta charset="utf-8">
<title>Calloway Business Centers</title>
<link rel="stylesheet" href="https://fonts.googleapis.com/css2?family=Asap:wght@400;500;700&family=Arimo:wght@400;700&display=swap">
<style>
:root{
  --navy:#0b0b6e;
  --ink:#222;
  --muted:#666;
  --line:#d5d5d5;
  --band:#f3f3f3;
  --white:#fff;
  --social-active:#1da1f2;
  --social-idle:#b3b3b3;
}
*{box-sizing:border-box;margin:0;padding:0}
html,body{width:1200px;height:2326px;overflow:hidden;background:var(--white)}
body{position:relative;font-family:"Arimo",Arial,sans-serif;color:var(--ink)}
.abs{position:absolute}

/* header */
.site-header{position:absolute;left:0;top:0;width:1200px;height:104px;background:var(--white)}
.brand{position:absolute;left:78px;top:12px;display:flex;align-items:center;gap:14px}
.brand-mark{width:78px;height:78px;border-radius:50%;background:var(--navy)}
.brand-name{font-family:"Asap",sans-serif;color:var(--navy);font-weight:700;font-size:40px;line-height:1;letter-spacing:1px}
.brand-sub{font-family:"Asap",sans-serif;color:var(--navy);font-size:13px;letter-spacing:5px;margin-top:6px}
.social{position:absolute;left:898px;top:10px;display:flex;gap:10px}
.social span{width:37px;height:37px;border-radius:50%;background:var(--social-idle)}
.social span.active{background:var(--social-active)}
.main-nav{position:absolute;right:81px;top:62px;display:flex;gap:32px;font-family:"Asap",sans-serif;font-size:17px;color:var(--navy);text-transform:uppercase}
.main-nav a{color:inherit;text-decoration:none}
.main-nav a.current{color:var(--ink)}

/* hero */
.hero{position:absolute;left:0;top:104px;width:1200px;height:573px;
  background:linear-gradient(180deg,#c9d1d8 0%,#aeb7bf 45%,#7b8288 75%,#5d6266 100%)}
.hero h1{position:absolute;left:0;width:100%;top:208px;text-align:center;color:var(--white);
  font-family:"Arimo",sans-serif;font-weight:700;font-size:62px;line-height:68px;text-shadow:0 2px 6px rgba(0,0,0,.25)}

/* welcome */
.welcome{position:absolute;left:0;top:677px;width:1200px;height:210px;
  background:linear-gradient(180deg,#ececec 0%,#fafafa 50%,#f1f1f1 100%);border-bottom:1px solid #e2e2e2;text-align:center}
.section-title{font-family:"Asap",sans-serif;font-weight:400;font-size:42px;color:var(--ink);letter-spacing:.5px}
.section-title em{font-style:normal;color:var(--navy);font-weight:500}
.welcome .section-title{margin-top:46px}
.welcome p{margin:18px auto 0;width:760px;font-size:17px;line-height:25px;color:var(--muted)}

/* services */
.services{position:absolute;left:0;top:887px;width:1200px;height:520px;text-align:center}
.services .section-title{margin-top:48px}
.service-cards{position:absolute;left:79px;top:127px;display:flex;gap:15px}
.card{width:198px;height:342px;border:1.5px solid var(--line);background:var(--white);padding-top:23px}
.card .icon{width:104px;height:104px;border-radius:50%;background:var(--navy);margin:0 auto;display:flex;align-items:center;justify-content:center}
.card h3{font-family:"Asap",sans-serif;font-weight:400;font-size:19px;line-height:23px;margin-top:20px;text-transform:uppercase;color:var(--ink)}
.card ul{list-style:none;margin-top:15px;font-family:"Asap",sans-serif;font-size:13.5px;line-height:23px;color:#444}

/* about */
.about{position:absolute;left:0;top:1407px;width:1200px;height:365px;background:var(--band)}
.video-frame{position:absolute;left:78px;top:53px;width:499px;height:262px;border-radius:14px 14px 6px 6px;
  background:linear-gradient(180deg,#8d8f92 0%,#6b6660 60%,#b9b9bb 100%)}
.play{position:absolute;left:218px;top:88px;width:62px;height:62px;border:3px solid var(--white);border-radius:50%}
.play::after{content:"";position:absolute;left:22px;top:16px;border-left:20px solid var(--white);border-top:12px solid transparent;border-bottom:12px solid transparent}
.about p{position:absolute;left:625px;top:50px;width:495px;font-size:14.4px;line-height:23.2px;color:#555}
.btn{display:inline-flex;align-items:center;justify-content:center;background:var(--navy);color:var(--white);
  font-family:"Arimo",sans-serif;border-radius:3px;text-decoration:none}
.about .btn{position:absolute;left:622px;top:261px;width:187px;height:50px;font-size:17px}

/* partners */
.partners{position:absolute;left:0;top:1772px;width:1200px;height:135px;background:var(--white);
  display:flex;align-items:center;justify-content:space-between;padding:0 92px}
.partner{width:150px;height:46px;border-radius:23px;background:#d4d4d4}
.partner.square{width:110px;border-radius:6px}

/* contact */
.contact{position:absolute;left:0;top:1907px;width:1200px;height:365px;background:var(--band)}
.contact .section-title{position:absolute;left:0;width:100%;top:37px;text-align:center}
.field{position:absolute;background:var(--band);border:1.5px solid #cfcfcf;border-radius:3px;
  font-size:14px;color:#a5a5a5;padding:0 0 0 44px;display:flex;align-items:center}
.field svg{position:absolute;left:15px}
.field.message{align-items:flex-start;padding-top:14px}
.field.message svg{top:14px}
.contact .btn{position:absolute;left:380px;top:260px;width:186px;height:53px;font-size:22px;letter-spacing:.5px}
.info{position:absolute;left:801px;font-size:14.5px;line-height:23px;color:#888}
.info svg{position:absolute;left:0;top:4px}
.info div{margin-left:33px}
.info .name{color:var(--navy)}

/* footer */
.site-footer{position:absolute;left:0;top:2272px;width:1200px;height:54px;background:var(--navy);
  color:var(--white);font-family:"Asap",sans-serif;font-size:15px;display:flex;align-items:center;justify-content:center}
.site-footer span{color:#9aa6ff;margin:0 4px}
</style>
</head>
<body>

<header class="site-header">
  <div class="brand">
    <div class="brand-mark"></div>
    <div>
      <div class="brand-name">CALLOWAY</div>
      <div class="brand-sub">BUSINESS CENTERS</div>
    </div>
  </div>
  <div class="social" aria-label="Social links"><span class="active"></span><span></span><span></span><span></span><span></span></div>
  <nav class="main-nav">
    <a class="current" href="#">Home</a>
    <a href="#">Properties</a>
    <a href="#">Virtual Tours &amp; Videos</a>
    <a href="#">Photos</a>
    <a href="#">Broker Referrals</a>
  </nav>
</header>

<section class="hero" role="img" aria-label="Photo of business people in a glass-walled meeting room on a video conference call">
  <h1>Stress Free, Affordable<br>Video Conferencing.</h1>
</section>

<section class="welcome">
  <h2 class="section-title">WELCOME TO <em>CALLOWAY</em></h2>
  <p>Come See Why Smarter Companies are Choosing Calloway Business Centers' Dallas, Ft. Worth and Houston Executive Office Suites, Virtual Offices, Meeting Rooms and Video Conferencing.</p>
</section>

<section class="services">
  <h2 class="section-title">OUR <em>SERVICES</em></h2>
  <div class="service-cards">
    <div class="card">
      <div class="icon"><svg width="54" height="54" viewBox="0 0 54 54" fill="none" stroke="#fff" stroke-width="2.5"><rect x="20" y="8" width="14" height="16" rx="2"/><line x1="6" y1="30" x2="48" y2="30"/><line x1="10" y1="30" x2="10" y2="46"/><line x1="44" y1="30" x2="44" y2="46"/><line x1="27" y1="24" x2="27" y2="30"/><rect x="34" y="30" width="10" height="8"/></svg></div>
      <h3>Executive Office<br>Suites</h3>
      <ul><li>Full Service Offices</li><li>Flexible Contracts from $395</li><li>Corporate or Satellite Office</li><li>Disaster Recovery</li><li>All-Inclusive Pricing!</li></ul>
    </div>
    <div class="card">
      <div class="icon"><svg width="56" height="54" viewBox="0 0 56 54" fill="none" stroke="#fff" stroke-width="2.5"><circle cx="18" cy="14" r="5"/><circle cx="38" cy="14" r="5"/><circle cx="11" cy="30" r="4"/><circle cx="45" cy="30" r="4"/><rect x="16" y="26" width="24" height="12" rx="3"/><line x1="10" y1="44" x2="46" y2="44"/></svg></div>
      <h3>On-Demand<br>Meeting Rooms</h3>
      <ul><li>On-Demand Options</li><li>Boardrooms $30/hr</li><li>Conference Rooms $20/hr</li><li>On-Demand Offices $15/hr</li><li>No Booking Fees!</li></ul>
    </div>
    <div class="card">
      <div class="icon"><svg width="56" height="54" viewBox="0 0 56 54" fill="none" stroke="#fff" stroke-width="2.5"><rect x="20" y="8" width="28" height="18"/><circle cx="11" cy="16" r="4"/><line x1="11" y1="20" x2="11" y2="40"/><line x1="11" y1="24" x2="22" y2="18"/><line x1="20" y1="40" x2="50" y2="40"/><circle cx="26" cy="34" r="3"/><circle cx="36" cy="34" r="3"/><circle cx="46" cy="34" r="3"/></svg></div>
      <h3>On-Demand<br>Training Rooms</h3>
      <ul><li>On-Demand Options</li><li>Training Rooms $ 50/hr</li><li>Computer Labs $ 50/hr</li><li>Catering Available</li><li>No Booking Fees!</li></ul>
    </div>
    <div class="card">
      <div class="icon"><svg width="56" height="54" viewBox="0 0 56 54" fill="none" stroke="#fff" stroke-width="2.5"><rect x="8" y="8" width="40" height="26"/><line x1="8" y1="38" x2="48" y2="38"/><circle cx="20" cy="28" r="3"/><circle cx="36" cy="28" r="3"/><line x1="14" y1="38" x2="14" y2="46"/><line x1="42" y1="38" x2="42" y2="46"/></svg></div>
      <h3>Virtual Office<br>Solutions</h3>
      <ul><li>Mailing Address $49/mo</li><li>Local Phone &amp; Mail $99/mo</li><li>Flexible Contracts</li><li>Corporate or Satellite Office</li><li>All-Inclusive Pricing!</li></ul>
    </div>
    <div class="card">
      <div class="icon"><svg width="56" height="54" viewBox="0 0 56 54" fill="none" stroke="#fff" stroke-width="2.5"><rect x="14" y="6" width="28" height="20"/><circle cx="28" cy="14" r="3"/><line x1="28" y1="26" x2="28" y2="32"/><rect x="16" y="32" width="24" height="6"/><circle cx="9" cy="30" r="3"/><circle cx="47" cy="30" r="3"/><line x1="9" y1="34" x2="9" y2="46"/><line x1="47" y1="34" x2="47" y2="46"/></svg></div>
      <h3>Video Conference<br>Solutions</h3>
      <ul><li>On-Demand Options</li><li>Bridging Service $ 50/hr</li><li>IP from $175/hr</li><li>Complimentary Test Call</li><li>No Booking Fees!</li></ul>
    </div>
  </div>
</section>

<section class="about">
  <div class="video-frame" role="img" aria-label="Video still of a team working together at a table, shown on a laptop screen">
    <div class="play"></div>
  </div>
  <p>Calloway Business Centers positions its management team in every one of its business centers - we operate with an open-door policy as a medium-sized company without all of the corporate bureaucracy and red tape. The service we provide in terms of technology is unparalleled in our industry. We outfit each of our locations with 100Mbps of bandwidth! We have the latest systems in place, with all locations offering IP PBX telephone systems, Corvane IP telephones and ReachLine Technology including Voicemail to Email and Faxdesk, with local technical support.</p>
  <a class="btn" href="#">VIEW MORE INFO</a>
</section>

<section class="partners" aria-label="Client partners">
  <div class="partner"></div>
  <div class="partner"></div>
  <div class="partner square"></div>
  <div class="partner"></div>
  <div class="partner"></div>
  <div class="partner square"></div>
</section>

<section class="contact">
  <h2 class="section-title">CONTACT <em>US</em></h2>
  <div class="field" style="left:78px;top:136px;width:291px;height:51px">
    <svg width="16" height="16" viewBox="0 0 16 16" fill="#bdbdbd"><circle cx="8" cy="5" r="4"/><path d="M0 16c0-5 4-7 8-7s8 2 8 7z"/></svg>Your Name:</div>
  <div class="field" style="left:78px;top:198px;width:291px;height:51px">
    <svg width="16" height="12" viewBox="0 0 16 12" fill="#bdbdbd"><rect width="16" height="12" rx="1"/><path d="M0 1l8 6 8-6" stroke="#f3f3f3" fill="none" stroke-width="1.5"/></svg>E-Mail Address:</div>
  <div class="field" style="left:78px;top:260px;width:291px;height:53px">
    <svg width="13" height="16" viewBox="0 0 13 16" fill="#bdbdbd"><path d="M0 0h9l4 4v12H0z"/></svg>Subject:</div>
  <div class="field message" style="left:380px;top:136px;width:374px;height:115px">
    <svg width="16" height="16" viewBox="0 0 16 16" fill="#bdbdbd"><path d="M11 1l4 4-9 9H2v-4z"/></svg>Message:</div>
  <a class="btn" href="#">SUBMIT</a>

  <div class="info" style="top:141px">
    <svg width="16" height="20" viewBox="0 0 16 20" fill="#0b0b6e"><path d="M8 0a8 8 0 0 1 8 8c0 6-8 12-8 12S0 14 0 8a8 8 0 0 1 8-8z"/><circle cx="8" cy="8" r="3" fill="#f3f3f3"/></svg>
    <div><span class="name">Calloway Business Centers</span><br>2140 Larkspur Avenue, Suite 300,<br>Dallas, Texas 75201</div>
  </div>
  <div class="info" style="top:211px">
    <svg width="16" height="16" viewBox="0 0 16 16" fill="#0b0b6e"><path d="M3 0l3 4-2 2c1 2 4 5 6 6l2-2 4 3-2 3C7 16 0 9 0 3z"/></svg>
    <div>Dallas - 214.555.0184<br>Houston - 713.555.0126</div>
  </div>
  <div class="info" style="top:269px">
    <svg width="18" height="14" viewBox="0 0 18 14" fill="#0b0b6e"><rect width="18" height="14" rx="1"/><path d="M0 1l9 7 9-7" stroke="#f3f3f3" fill="none" stroke-width="1.5"/></svg>
    <div>Offices@CallowayOffices.com</div>
  </div>
</section>

<footer class="site-footer">© <span>Calloway Business Centers</span> - 2016. All Rights Reserved.</footer>

</body>
</html>
```